K & R Acre Works. Business card design

We need a business card designed for a new business. We have a bulldozer and tractor service. We clear land and make wildlife food plots. We provide disking, bush hogging, and site prep services.
I have attached an image of a business card that I like and would like my business cards to look similar.

Target Market(s)

anyone needing bulldozer and/or tractor services

Industry/Entity Type

Business

Contact Information for Business Card

K & R Acre Works, Operated by 7-T-Ranch
Wade Colton
601-472-3358
wcr4817@fieldmail-example.com

Font styles to use
Sans Serif

Colors

Designer to choose colors to be used in the design.

Requirements
Must have
• image of tractor and bulldozer
• Land Clearing
• Wildlife food plots
• Bush Hogging
• Disking
• Site prep
Nice to have
• i have included a image of a business card that i like. I would like mine to be similar.

```html
<!DOCTYPE html>
<html lang="en">
<head>
<meta charset="utf-8">
<title>K & R Acre Works — Business Card</title>
<link rel="stylesheet" href="https://fonts.googleapis.com/css2?family=Roboto+Condensed:wght@400;700&family=Roboto:wght@400&display=swap">
<style>
  :root {
    --page-bg: #e4e4e2;
    --card-bg: #f3f3f2;
    --olive: #949a35;
    --orange: #b25a16;
    --brown: #6b3e14;
    --ink: #4a4a4a;
    --rule: #c9c9c6;
    --dozer-tone: linear-gradient(160deg, #5d6a3e 0%, #8a8a5a 45%, #6b5a3c 100%);
    --tractor-tone: linear-gradient(160deg, #5e7a3a 0%, #a88f5c 55%, #c8552a 100%);
  }
  html, body {
    margin: 0;
    width: 1200px;
    height: 960px;
    overflow: hidden;
    background: var(--page-bg);
  }
  .card {
    position: absolute;
    left: 300px;
    top: 310px;
    width: 600px;
    height: 342px;
    background: var(--card-bg);
    font-family: "Roboto", sans-serif;
    color: var(--ink);
  }
  .brand {
    position: absolute;
    left: 54px;
    top: 96px;
    width: 274px;
  }
  .brand-name {
    display: flex;
    align-items: center;
    gap: 6px;
    font-family: "Roboto Condensed", sans-serif;
    font-weight: 700;
    font-size: 23px;
    line-height: 1;
    color: var(--brown);
    letter-spacing: 0.3px;
  }
  .brand-mark {
    width: 16px;
    height: 16px;
    background: var(--olive);
  }
  .brand-tagline {
    margin-top: 5px;
    font-family: "Roboto Condensed", sans-serif;
    font-weight: 700;
    font-size: 10.6px;
    color: #2e2e2e;
    letter-spacing: 0.2px;
  }
  .photo {
    position: absolute;
    top: 147px;
    height: 88px;
  }
  .photo-dozer { left: 54px; width: 148px; background: var(--dozer-tone); }
  .photo-tractor { left: 209px; width: 119px; background: var(--tractor-tone); }
  .divider {
    position: absolute;
    left: 355px;
    top: 60px;
    width: 1px;
    height: 210px;
    background: var(--rule);
  }
  .contact {
    position: absolute;
    left: 380px;
    top: 60px;
  }
  .person-name {
    font-family: "Roboto Condensed", sans-serif;
    font-weight: 700;
    font-size: 21px;
    color: var(--olive);
    line-height: 1;
  }
  .person-role {
    font-family: "Roboto Condensed", sans-serif;
    font-size: 16px;
    color: var(--brown);
    margin-top: 3px;
  }
  .contact-list, .service-list {
    list-style: none;
    margin: 0;
    padding: 0;
  }
  .contact-list { margin-top: 12px; }
  .contact-list li {
    display: flex;
    align-items: center;
    gap: 6px;
    font-size: 14.5px;
    line-height: 18px;
  }
  .contact-list svg { width: 13px; height: 13px; fill: var(--olive); }
  .services-title {
    margin-top: 11px;
    font-family: "Roboto Condensed", sans-serif;
    font-weight: 700;
    font-size: 17px;
    color: var(--olive);
  }
  .service-list li {
    font-size: 14.5px;
    line-height: 18px;
  }
  .bullet { color: var(--olive); margin-right: 7px; }
  .bullet-inline { color: var(--olive); margin: 0 3px; }
  .color-band {
    position: absolute;
    left: 0;
    bottom: 0;
    width: 600px;
    height: 17px;
    display: flex;
    gap: 2px;
  }
  .band-olive { width: 197px; background: var(--olive); }
  .band-orange { width: 202px; background: var(--orange); }
  .band-brown { flex: 1; background: var(--brown); }
</style>
</head>
<body>
  <div class="card">
    <div class="brand">
      <div class="brand-name"><span class="brand-mark"></span>K &amp; R ACRE WORKS</div>
      <div class="brand-tagline">FOR ALL OF YOUR LAND IMPROVEMENT NEEDS</div>
    </div>
    <div class="photo photo-dozer" role="img" aria-label="Photo of a yellow bulldozer pushing soil while clearing land"></div>
    <div class="photo photo-tractor" role="img" aria-label="Photo of an orange tractor with a front implement in a grassy field"></div>

    <div class="divider"></div>

    <div class="contact">
      <div class="person-name">WADE COLTON</div>
      <div class="person-role">OWNER</div>
      <ul class="contact-list">
        <li><svg viewBox="0 0 24 24"><path d="M6.6 10.8a15.1 15.1 0 0 0 6.6 6.6l2.2-2.2a1 1 0 0 1 1-.25 11.4 11.4 0 0 0 3.6.57 1 1 0 0 1 1 1V20a1 1 0 0 1-1 1A17 17 0 0 1 3 4a1 1 0 0 1 1-1h3.5a1 1 0 0 1 1 1c0 1.25.2 2.45.57 3.57a1 1 0 0 1-.25 1z"/></svg>601-472-3358</li>
        <li><svg viewBox="0 0 24 24"><path d="M2 5h20v14H2z M2 5l10 8 10-8" fill="none" stroke="#949a35" stroke-width="0"/><path d="M2 5h20v2l-10 7L2 7z"/><path d="M2 9l10 7 10-7v10H2z"/></svg>wcr4817@fieldmail-example.com</li>
        <li><svg viewBox="0 0 24 24"><circle cx="12" cy="12" r="10"/><path d="M2 12h20M12 2c3 3 3 17 0 20M12 2c-3 3-3 17 0 20" stroke="#f3f3f2" stroke-width="1.5" fill="none"/></svg>kracreworks-example.com</li>
      </ul>
      <div class="services-title">WE CREADED</div>
      <ul class="service-list">
        <li><span class="bullet">•</span>Land Clearing</li>
        <li><span class="bullet">•</span>Wildlife food plots</li>
        <li><span class="bullet">•</span>Bush Hogging</li>
        <li><span class="bullet">•</span>Disking<span class="bullet-inline">•</span>Site prep</li>
      </ul>
    </div>

    <div class="color-band">
      <div class="band-olive"></div>
      <div class="band-orange"></div>
      <div class="band-brown"></div>
    </div>
  </div>
</body>
</html>
```